Design and Renovation Company Luxury Business Card

I want to create a luxury business card for a Design and Renovation Firm . We will use our current logo. The company name is 528BUILDA. We do not want anything standard. We need a very unique concept.
Please see uploaded inspiration. I really like the textured paper option. I would like the card to be thick with debossing, and/or embossing options. The logo has orange in it but I would like to see the card with and without the orange. I think the orange may make the company feel less high-end. The goal is to elevate the logo not match its vibe per se of the logo. We want something very unique, not standard at all!
I would like a space for :
Logo,
Name,
Position,
Email,
Office number,
Website Address,
Business Address,
Thank you!
Have fun!
Target Market(s)
Home owners Age 35 +
Industry/Entity Type
Design and Renovation
Contact Information for Business Card
Logo, Name, Position, Email, Office number, Website Address, Business Address,.
Colors
Designer to choose colors to be used in the design.
Requirements
Must have
- A luxury designer feel. Must be black or dark grey but open to other luxury ideas.
Nice to have
- Gold, silver, black embossing or debossing. Textured paper design.
Should not have
- A cheap look and feel.

```html
<!DOCTYPE html>
<html lang="en">
<head>
<meta charset="utf-8">
<title>528BUILDA – Business Card</title>
<link href="https://fonts.googleapis.com/css2?family=Montserrat:wght@400;500;700&display=swap" rel="stylesheet">
<style>
  :root {
    --backdrop: #9a9a9a;
    --paper: #ffffff;
    --ink: #111111;
    --accent: #f39222;
    --card-dark: #1b1b1b;
    --deboss: #0e0e0e;
  }
  * { box-sizing: border-box; margin: 0; padding: 0; }
  html, body { width: 1093px; height: 1200px; overflow: hidden; }
  body {
    background: var(--backdrop);
    font-family: "Montserrat", Arial, sans-serif;
    color: var(--ink);
    position: relative;
  }
  .card {
    position: absolute;
    left: 264px;
    width: 597px;
  }
  .card-front { top: 225px; height: 363px; background: var(--paper); }
  .card-back  { top: 616px; height: 366px; background: var(--card-dark); }

  .brand-name {
    position: absolute;
    font-weight: 700;
    line-height: 1;
    white-space: nowrap;
  }
  .card-front .brand-name {
    left: 20px; top: 36px;
    font-size: 26px; letter-spacing: 1px;
    color: var(--ink);
  }
  .card-back .brand-name {
    left: 50%; top: 178px; transform: translateX(-50%);
    font-size: 44px; letter-spacing: 2px;
    color: var(--deboss);
  }

  .person { position: absolute; right: 29px; top: 22px; text-align: right; }
  .person-name { font-size: 23px; font-weight: 700; line-height: 1.15; }
  .person-role { font-size: 14px; font-weight: 400; margin-top: 2px; }

  .contacts { position: absolute; left: 27px; top: 274px; list-style: none; }
  .contacts li {
    display: flex; align-items: center; gap: 7px;
    font-size: 14px; height: 23.5px;
  }
  .contacts svg { width: 13px; height: 13px; flex: none; }

  .address {
    position: absolute; left: 390px; top: 307px;
    font-size: 14px; font-style: normal; line-height: 1.2;
  }
</style>
</head>
<body>
  <section class="card card-front">
    <div class="brand-name">528BUILDA</div>

    <div class="person">
      <div class="person-name">Daniel Hartwell</div>
      <div class="person-role">Managing Director</div>
    </div>

    <ul class="contacts">
      <li>
        <svg viewBox="0 0 16 16" aria-hidden="true"><path fill="var(--accent)" d="M3.2 1.2l2.2 2.6-1.3 1.6c.9 2 2.4 3.6 4.5 4.6l1.5-1.3 2.7 2.2-1.3 2.4C6.3 13.3 2.6 9.6 1 4.4z"/><path fill="none" stroke="var(--accent)" stroke-width="1.3" d="M9.5 1.5a5 5 0 0 1 5 5M9.3 4a2.6 2.6 0 0 1 2.7 2.6"/></svg>
        <span>614-555-0193</span>
      </li>
      <li>
        <svg viewBox="0 0 16 16" aria-hidden="true"><rect x="1" y="3.5" width="14" height="9" rx="1" fill="var(--accent)"/><path d="M1.5 4.3 8 9l6.5-4.7" fill="none" stroke="#fff" stroke-width="1.1"/></svg>
        <span>info@528builda-studio.com</span>
      </li>
      <li>
        <svg viewBox="0 0 16 16" aria-hidden="true"><circle cx="8" cy="8" r="7" fill="var(--accent)"/><path d="M4 4.5c1.5.3 2 1.3 1.6 2.4-.5 1 .7 1.6 1.2 2.5.4.9-.2 2-.5 3M10 2.5c-.6 1.2.4 2.1 1.6 2.3 1 .2 1.3 1.3.7 2.4" fill="none" stroke="#fff" stroke-width="1.2"/></svg>
        <span>www.528builda-studio.com</span>
      </li>
    </ul>

    <address class="address">
      418 Linden Park Ave, #112<br>
      Marlow Heights, OH 43071
    </address>
  </section>

  <section class="card card-back">
    <div class="brand-name">528BUILDA</div>
  </section>
</body>
</html>
```